Upmarket Dessert Lounge needs a Business Card Design

We are an upmarket dessert lounge needing a business card to match our image.

We want something that is simple yet beautiful, feminine, classy, sophisticated and elegant. We want it to stand out and don't mind if it is bold.

The design should include our logo and colours of red or maroon with gold highlights. We don't mind if black is used.

Marlow & Quince

Target Market(s)

For those who like to indulge or treat themselves and give in to their temptations on good quality desserts.

Industry/Entity Type

Business

Requirements
Must have
• Must include our logo and our name

Marlow & Quince

M & Q

```html
<!DOCTYPE html>
<html lang="en">
<head>
<meta charset="utf-8">
<title>Marlow &amp; Quince — Business Card</title>
<link rel="stylesheet" href="https://fonts.googleapis.com/css2?family=Open+Sans:wght@400;700&display=swap">
<style>
  :root {
    --stage: #d9d9d9;
    --card-black: #000000;
    --maroon: #7a1315;
    --cream: #fdd49a;
    --ink: #1a1a1a;
    --white: #ffffff;
  }
  html, body {
    margin: 0;
    padding: 0;
    width: 956px;
    height: 1200px;
    overflow: hidden;
    background: var(--stage);
    font-family: "Open Sans", Arial, sans-serif;
  }
  .canvas {
    position: relative;
    width: 956px;
    height: 1200px;
  }
  .card {
    position: absolute;
    width: 798px;
    height: 455px;
    border-radius: 28px;
    background: var(--card-black);
    overflow: hidden;
  }
  .card--front { left: 79px; top: 85px; }
  .card--back  { left: 73px; top: 632px; }

  .brand-name {
    position: absolute;
    left: 0;
    right: 0;
    text-align: center;
    color: var(--cream);
    font-weight: 400;
    letter-spacing: 1px;
    margin: 0;
  }
  .card--front .brand-name {
    top: 112px;
    font-size: 40px;
  }
  .card--back .brand-name {
    top: 180px;
    font-size: 84px;
    line-height: 1;
  }

  .info-band {
    position: absolute;
    left: 0;
    top: 290px;
    width: 798px;
    height: 97px;
  }
  .info-band .band-maroon { fill: var(--maroon); }
  .info-band .band-cream  { fill: var(--cream); }

  .holder {
    position: absolute;
    left: 60px;
    top: 314px;
    color: var(--white);
    line-height: 1.25;
  }
  .holder__name {
    display: block;
    font-weight: 700;
    font-size: 20px;
  }
  .holder__role {
    display: block;
    font-size: 20px;
    letter-spacing: 0.5px;
  }

  .contact {
    position: absolute;
    right: 24px;
    top: 298px;
    text-align: right;
    color: var(--ink);
    font-size: 18px;
    line-height: 29.5px;
    margin: 0;
  }
  .contact b { font-weight: 700; }

  .phones {
    position: absolute;
    left: 0;
    right: 0;
    top: 408px;
    text-align: center;
    color: var(--white);
    font-size: 20px;
    margin: 0;
  }
  .phones b { font-weight: 700; }
  .phones .sep { margin: 0 8px; }
</style>
</head>
<body>
<main class="canvas">

  <section class="card card--front" aria-label="Business card front">
    <h1 class="brand-name">MARLOW &amp; QUINCE</h1>

    <svg class="info-band" viewBox="0 0 798 97" aria-hidden="true">
      <polygon class="band-maroon" points="0,0 361,0 273,97 0,97"/>
      <polygon class="band-cream" points="381,0 798,0 798,97 293,97"/>
    </svg>

    <div class="holder">
      <span class="holder__name">Your Name</span>
      <span class="holder__role">Designation</span>
    </div>

    <p class="contact">
      <b>e</b> : name@yourwebsite.com<br>
      <b>w</b> : www.marlowquince.com<br>
      0000, Street Name, City Name, Country Code.
    </p>

    <p class="phones">
      <b>p</b> : 123-456-7890<span class="sep">|</span><b>c</b> : 123-456-7890<span class="sep">|</span><b>f</b> : 123-456-7890
    </p>
  </section>

  <section class="card card--back" aria-label="Business card back">
    <p class="brand-name">M &amp; Q</p>
  </section>

</main>
</body>
</html>
```